Ashbury Climate Business Card Design

Design new, 2 sides, business cards for a residential and light commercial heating, air conditioning contractor.

Target Market(s)

Homeowners, small businesses

Industry/Entity Type

Business

Contact Information for Business Card

Dominic Westerhall
Phone - 862-415-2736
Email
Address - PO box 518
Brightwater NJ 07912
Website - www.HarborBreezeLLC.example

Requirements
Must have
• logo, company colors, standard size with no die cut, so I can use nova stamp

```html
<!DOCTYPE html>
<html lang="en">
<head>
<meta charset="utf-8">
<title>Ashbury Climate Business Card</title>
<link rel="stylesheet" href="https://fonts.googleapis.com/css2?family=Source+Sans+3:wght@400;600;700&family=Tinos&display=swap">
<style>
  :root {
    --backdrop: #7c1517;
    --card-white: #f3f2f0;
    --ink-grey: #555555;
    --brand-red: #b5171d;
    --brand-orange: #e0590f;
    --flame-red: #c41a24;
    --flame-orange: #ef7a12;
    --sky-top: #a9cbef;
    --sky-bottom: #e2ebf4;
    --ink-dark: #1c1c1c;
  }
  html, body {
    margin: 0;
    padding: 0;
    width: 1200px;
    height: 987px;
    overflow: hidden;
    background: var(--backdrop);
  }
  .canvas {
    position: relative;
    width: 1200px;
    height: 987px;
  }
  .card {
    position: absolute;
    width: 615px;
    height: 352px;
    overflow: hidden;
    box-shadow: 0 4px 10px rgba(0, 0, 0, 0.45);
  }
  /* Front */
  .card-front {
    left: 250px;
    top: 131px;
    background: var(--card-white);
    font-family: "Source Sans 3", "Myriad Pro", sans-serif;
    color: var(--ink-grey);
  }
  .contact {
    position: absolute;
    left: 43px;
    top: 44px;
  }
  .contact-name {
    margin: 0;
    font-size: 29px;
    font-weight: 700;
    line-height: 1;
    color: var(--brand-red);
    letter-spacing: 0.3px;
  }
  .contact-title {
    margin: 5px 0 0;
    font-size: 17px;
    font-weight: 600;
    color: var(--brand-orange);
  }
  .contact-email {
    margin: 2px 0 0;
    font-size: 16px;
  }
  .contact-address {
    margin: 23px 0 0;
    font-size: 16px;
    font-style: normal;
    line-height: 22px;
  }
  .contact-phones {
    margin: 10px 0 0;
    padding: 0;
    list-style: none;
    font-size: 16px;
    line-height: 23.5px;
  }
  .phone-label {
    color: var(--brand-orange);
    font-weight: 700;
  }
  .contact-web {
    margin: 18px 0 0;
    font-size: 16px;
    color: var(--brand-orange);
  }
  .flame-art {
    position: absolute;
    right: 0;
    top: 0;
    width: 230px;
    height: 352px;
    border-radius: 120px 0 0 40px;
    background: linear-gradient(180deg, var(--flame-red) 0%, var(--flame-orange) 100%);
  }
  /* Back */
  .card-back {
    left: 384px;
    top: 534px;
    background: linear-gradient(180deg, var(--sky-top) 0%, var(--sky-bottom) 100%);
    text-align: center;
  }
  .brand-name {
    position: absolute;
    left: 0;
    right: 0;
    top: 128px;
    margin: 0;
    font-family: "Source Sans 3", "Myriad Pro", sans-serif;
    font-size: 50px;
    font-weight: 700;
    line-height: 1.2;
    color: var(--brand-red);
    letter-spacing: 1px;
  }
  .services {
    position: absolute;
    left: 0;
    right: 0;
    top: 263px;
    margin: 0;
    font-family: "Tinos", "Times New Roman", serif;
    font-size: 18px;
    line-height: 22px;
    color: var(--ink-dark);
  }
</style>
</head>
<body>
<main class="canvas">
  <section class="card card-front" aria-label="Business card front">
    <div class="contact">
      <h1 class="contact-name">DOMINIC WESTERHALL</h1>
      <p class="contact-title">CEO/FOUNDER</p>
      <p class="contact-email">dominic@ashburyclimatellc.example</p>
      <address class="contact-address">PO box 518<br>Brightwater NJ 07912</address>
      <ul class="contact-phones">
        <li><span class="phone-label">(P)</span> 862 415 2736</li>
        <li><span class="phone-label">(M)</span> 862 415 2790</li>
        <li><span class="phone-label">(F)</span> 862 415 2741</li>
      </ul>
      <p class="contact-web">www.AshburyClimateLLC.example</p>
    </div>
    <div class="flame-art" role="img" aria-label="Large red-to-orange flame illustration"></div>
  </section>

  <section class="card card-back" aria-label="Business card back">
    <h2 class="brand-name">Ashbury Climate</h2>
    <p class="services">Residential &amp; light commercial heating<br>Air conditioning contractor</p>
  </section>
</main>
</body>
</html>
```